Home Loan Introducer needs logo/business cards

We need a simple but classy logo for business cards and flyers. The business is a home loan referral business that is called an Introducer. The business name is "The Harborline".
I was thinking very simple and straight to the point on the front with "Home Loans" the only thing on the front with a nice background colour/s.
Then on the back, "The Harborline"
and "Quality Customer Service"
and "Email, text or call welcome"
and then my name, email address and phone number.
Updates
Thank you for all the designs :-)
Target Market(s)
Home buyers.
Home owners.
Investors.
Industry/Entity Type
Loan
Look and feel

```html
<!DOCTYPE html>
<html lang="en">
<head>
<meta charset="utf-8">
<title>The Harborline – Home Loan Business Cards</title>
<link rel="stylesheet" href="https://fonts.googleapis.com/css2?family=Exo+2:wght@500;700;800&display=swap">
<style>
  :root {
    --backdrop: #e9e6e1;
    --brand-blue: #0a67b3;
    --brand-orange: #fbab33;
    --paper-white: #ffffff;
    --ink-dark: #1d3f66;
    --card-shadow: 0 14px 30px rgba(0, 0, 0, 0.25);
  }
  * { box-sizing: border-box; margin: 0; padding: 0; }
  html, body {
    width: 1200px;
    height: 750px;
    overflow: hidden;
  }
  body {
    background: var(--backdrop);
    font-family: "Exo 2", "Trebuchet MS", sans-serif;
  }
  .canvas {
    position: relative;
    width: 1200px;
    height: 750px;
  }
  .card {
    position: absolute;
    top: 232px;
    width: 500px;
    height: 286px;
    box-shadow: var(--card-shadow);
    overflow: hidden;
  }
  /* Front */
  .card-front {
    left: 60px;
    background: var(--brand-blue);
  }
  .headline-bar {
    position: absolute;
    left: 44px;
    top: 112px;
    width: 412px;
    height: 72px;
    background: var(--brand-orange);
    border-radius: 8px;
    display: flex;
    align-items: center;
    justify-content: center;
  }
  .headline {
    color: var(--paper-white);
    font-weight: 800;
    font-size: 50px;
    letter-spacing: 1px;
    line-height: 1;
    text-transform: uppercase;
  }
  /* Back */
  .card-back {
    left: 640px;
    background: var(--brand-orange);
  }
  .back-top {
    position: absolute;
    inset: 0 0 auto 0;
    height: 112px;
    background: var(--paper-white);
  }
  .brand-lockup {
    position: absolute;
    left: 0;
    right: 0;
    top: 78px;
    display: flex;
    align-items: center;
    justify-content: center;
    gap: 12px;
  }
  .brand-dot {
    width: 34px;
    height: 34px;
    border-radius: 50%;
    background: var(--brand-blue);
  }
  .brand-name {
    color: var(--brand-blue);
    font-weight: 700;
    font-size: 28px;
    text-transform: uppercase;
    letter-spacing: 0.5px;
  }
  .service-list {
    position: absolute;
    left: 150px;
    top: 140px;
    list-style: none;
    color: var(--brand-blue);
    font-weight: 500;
    font-size: 15px;
    line-height: 20px;
  }
  .service-list li {
    display: flex;
    align-items: center;
    gap: 6px;
  }
  .tick { width: 14px; height: 14px; }
  .contact {
    position: absolute;
    left: 0;
    right: 0;
    top: 192px;
    text-align: center;
  }
  .contact-name {
    color: var(--brand-blue);
    font-weight: 700;
    font-size: 22px;
    line-height: 26px;
  }
  .contact-rule {
    width: 190px;
    height: 2px;
    margin: 2px auto 4px;
    background: var(--paper-white);
  }
  .contact-detail {
    color: var(--paper-white);
    font-weight: 500;
    font-size: 11px;
    line-height: 14px;
  }
</style>
</head>
<body>
<main class="canvas">
  <section class="card card-front" aria-label="Business card front">
    <div class="headline-bar">
      <h1 class="headline">Home Loan</h1>
    </div>
  </section>

  <section class="card card-back" aria-label="Business card back">
    <div class="back-top"></div>
    <div class="brand-lockup">
      <span class="brand-dot" aria-hidden="true"></span>
      <span class="brand-name">The Harborline</span>
    </div>
    <ul class="service-list">
      <li>
        <svg class="tick" viewBox="0 0 14 14" aria-hidden="true"><path d="M2 7.5 L5.5 11 L12 3" fill="none" stroke="#ffffff" stroke-width="2.4" stroke-linecap="round" stroke-linejoin="round"/></svg>
        Quality Customer Service
      </li>
      <li>
        <svg class="tick" viewBox="0 0 14 14" aria-hidden="true"><path d="M2 7.5 L5.5 11 L12 3" fill="none" stroke="#ffffff" stroke-width="2.4" stroke-linecap="round" stroke-linejoin="round"/></svg>
        Email, text or call welcome
      </li>
    </ul>
    <div class="contact">
      <p class="contact-name">Dana Mercer</p>
      <div class="contact-rule"></div>
      <p class="contact-detail">Phone: +610555018</p>
      <p class="contact-detail">Email: dana@harborline.example</p>
    </div>
  </section>
</main>
</body>
</html>
```